Dr Peter Holm
Urologist
Professional
Dr Peter Holm MB,ChB(FHU), FC Urol.(SA)
Ravenscliff Healthcare Centre and Thornvale Private Hospital PO Box 58140 Fernbrook 3174
pholm@veltramail.co.za
Pr No 7318564
Please email me for scanned copies of the existing stationery and cards to see current format

```html
<!DOCTYPE html>
<html lang="en">
<head>
<meta charset="utf-8">
<title>Dr Peter Holm – Urologist Stationery</title>
<link rel="stylesheet" href="https://fonts.googleapis.com/css2?family=EB+Garamond:wght@400;500;600&display=swap">
<style>
  :root {
    --backdrop: #e8e5e0;
    --paper: #fbf9f0;
    --paper-white: #ffffff;
    --brand-red: #8a1a1c;
    --brand-red-dark: #5e0f12;
    --ink: #3a3a3a;
    --ink-soft: #6b6b6b;
    --shadow: rgba(0,0,0,0.18);
  }
  * { box-sizing: border-box; margin: 0; padding: 0; }
  html, body { width: 1200px; height: 679px; overflow: hidden; }
  body {
    background: var(--backdrop);
    font-family: "EB Garamond", Georgia, serif;
    color: var(--ink);
    position: relative;
  }
  .sheet { position: absolute; box-shadow: 0 3px 10px var(--shadow); overflow: hidden; }
  .sheet svg.wave { position: absolute; inset: 0; width: 100%; height: 100%; }
  .name { color: var(--brand-red); font-weight: 600; line-height: 1; }
  .quals { color: var(--ink-soft); letter-spacing: 0.04em; line-height: 1.2; }
  .specialty { color: var(--brand-red); font-weight: 600; line-height: 1; }
  .contact { color: var(--ink); line-height: 1.35; }
  .contact p { white-space: nowrap; }
  .contact .gap { margin-top: 6px; }

  /* Business card */
  .card { left: 50px; top: 252px; width: 280px; height: 166px; background: var(--paper-white); }
  .card .identity { position: absolute; left: 0; right: 0; top: 14px; text-align: center; }
  .card .name { font-size: 15px; }
  .card .quals { font-size: 6px; margin-top: 2px; }
  .card .specialty { font-size: 17px; margin-top: 7px; }
  .card .contact { position: absolute; left: 66px; top: 70px; font-size: 5.5px; }

  /* Letterhead */
  .letterhead { left: 360px; top: 28px; width: 420px; height: 624px; background: var(--paper); }
  .letterhead .identity { position: absolute; left: 52px; top: 34px; }
  .letterhead .name { font-size: 16px; }
  .letterhead .quals { font-size: 6.5px; margin-top: 2px; }
  .letterhead .specialty { font-size: 21px; margin-top: 12px; }
  .letterhead .contact { position: absolute; left: 52px; top: 112px; font-size: 6.5px; }

  /* Compliment slip */
  .slip { left: 810px; top: 104px; width: 340px; height: 164px; background: var(--paper-white); }
  .slip .identity { position: absolute; left: 28px; top: 14px; }
  .slip .name { font-size: 13px; }
  .slip .quals { font-size: 5.5px; margin-top: 2px; }
  .slip .specialty { font-size: 16px; margin-top: 7px; }
  .slip .contact { position: absolute; left: 28px; top: 64px; font-size: 5.5px; }

  /* Envelope */
  .envelope { left: 810px; top: 330px; width: 340px; height: 200px; background: var(--paper-white); }
  .envelope .flap-name { position: absolute; left: 0; right: 0; top: 22px; text-align: center; color: var(--paper-white); }
  .envelope .flap-name .name { color: var(--paper-white); font-size: 13px; }
  .envelope .flap-name .quals { color: #f1dede; font-size: 5.5px; margin-top: 2px; }
  .envelope .front-name { position: absolute; left: 0; right: 0; top: 118px; text-align: center; }
  .envelope .front-name .name { font-size: 13px; }
  .envelope .front-name .quals { font-size: 5.5px; margin-top: 2px; }
</style>
</head>
<body>

  <section class="sheet card">
    <svg class="wave" viewBox="0 0 280 166" preserveAspectRatio="none" aria-hidden="true">
      <path d="M0 122 C70 150 150 92 280 112 L280 166 L0 166 Z" fill="var(--brand-red)"/>
      <path d="M0 122 C70 150 150 92 280 112" fill="none" stroke="var(--brand-red-dark)" stroke-width="2"/>
      <path d="M0 118 C70 144 150 88 280 106" fill="none" stroke="var(--brand-red)" stroke-width="0.8"/>
    </svg>
    <div class="identity">
      <p class="name">Dr Peter Holm</p>
      <p class="quals">MB,ChB(FHU), FC Urol.(SA)</p>
      <p class="specialty">Urologist</p>
    </div>
    <div class="contact">
      <p>Ravenscliff Healthcare Centre and Thornvale Private Hospital</p>
      <p>PO Box 58140 Fernbrook 3174</p>
      <p>Tel 033 555 0142 &nbsp; Fax 033 555 0143</p>
      <p>pholm@veltramail.co.za &nbsp; Pr No 7318564</p>
    </div>
  </section>

  <section class="sheet letterhead">
    <svg class="wave" viewBox="0 0 420 624" preserveAspectRatio="none" aria-hidden="true">
      <path d="M0 0 L40 0 C40 120 14 200 16 320 C18 440 44 520 40 624 L0 624 Z" fill="var(--brand-red)"/>
      <path d="M40 0 C40 120 14 200 16 320 C18 440 44 520 40 624" fill="none" stroke="var(--brand-red-dark)" stroke-width="2"/>
      <path d="M46 0 C46 120 20 200 22 320 C24 440 50 520 46 624" fill="none" stroke="var(--brand-red)" stroke-width="0.8"/>
    </svg>
    <div class="identity">
      <p class="name">Dr Peter Holm</p>
      <p class="quals">MB,ChB(FHU), FC Urol.(SA)</p>
      <p class="specialty">Urologist</p>
    </div>
    <div class="contact">
      <p>Ravenscliff Healthcare Centre</p>
      <p>and Thornvale Private Hospital</p>
      <p class="gap">PO Box 58140</p>
      <p>Fernbrook 3174</p>
      <p class="gap">Tel 033 555 0142</p>
      <p>Fax 033 555 0143</p>
      <p>Cell 082 555 0190</p>
      <p class="gap">pholm@veltramail.co.za</p>
      <p>Pr No 7318564</p>
    </div>
  </section>

  <section class="sheet slip">
    <svg class="wave" viewBox="0 0 340 164" preserveAspectRatio="none" aria-hidden="true">
      <path d="M0 0 L16 0 C16 50 6 100 14 164 L0 164 Z" fill="var(--brand-red)"/>
      <path d="M16 0 C16 50 6 100 14 164" fill="none" stroke="var(--brand-red-dark)" stroke-width="1.5"/>
    </svg>
    <div class="identity">
      <p class="name">Dr Peter Holm</p>
      <p class="quals">MB,ChB(FHU), FC Urol.(SA)</p>
      <p class="specialty">Urologist</p>
    </div>
    <div class="contact">
      <p>Ravenscliff Healthcare Centre</p>
      <p>and Thornvale Private Hospital</p>
      <p class="gap">PO Box 58140 Fernbrook 3174</p>
      <p>pholm@veltramail.co.za</p>
    </div>
  </section>

  <section class="sheet envelope">
    <svg class="wave" viewBox="0 0 340 200" preserveAspectRatio="none" aria-hidden="true">
      <path d="M0 0 L340 0 L340 30 L170 78 L0 30 Z" fill="var(--brand-red)"/>
      <path d="M0 30 L170 78 L340 30" fill="none" stroke="var(--brand-red-dark)" stroke-width="1.5"/>
      <path d="M0 200 L150 110 M340 200 L190 110" stroke="#e4e4e4" stroke-width="1" fill="none"/>
    </svg>
    <div class="flap-name">
      <p class="name">Dr Peter Holm</p>
      <p class="quals">MB,ChB(FHU), FC Urol.(SA)</p>
    </div>
    <div class="front-name">
      <p class="name">Dr Peter Holm</p>
      <p class="quals">MB,ChB(FHU), FC Urol.(SA)</p>
    </div>
  </section>

</body>
</html>
```